Website design for legal tech start up in Switzerland (B2B)

We are for a legal tech start up in Switzerland called KOVA. We have been running since August 2016. This will be our first live website.

We need a website designed and business card design for our start-up in Switzerland. We also need the Web design to be converted into HTML and CSS files.

Function of website:
• To inform potential customers of our services
• Form a key part of our digital marketing and sales footprint.
• Branding

Please find attached logo.
Updates

Project Deadline Extended Reason: Giving us time to review submissions and provide opportunity for more submissions. Added Thursday, February 16, 2017

Project Deadline Extended
Reason: Looking for more idea's not necessarily set on blue and grey colours only.

Target Market(s)

B2B tech powered legal services.

Industry/Entity Type

Legal

Contact Information for Business Card

Lean and slick design.

Coding

Coded - Design and coding required

Number of Pages Required

5+ page

Requirements
Must have
• VERY LEAN AND CLEAN DESIGN!
• We have received many great standard designs, but we are looking for something more out-of-the box: You can get inspiration from these designs: http://www.pixelvane.com/websites/clean/
• Thanks!!
• Easy content management system
• Well structured coding for additional development
• Responsive webpage for all types of devices
• SEO optimized
• Tabs (Home, services, team, careers, blog, contact us)
• Colour scheme complementary to logo
Nice to have
• Look and Design - Approachable, High-tech, Modern
• Easy to add chat bot capability in future
Should not have
• Too busy/ too much clutter
• Not take to long to load

```html
<!DOCTYPE html>
<html lang="en">
<head>
<meta charset="utf-8">
<title>KOVA – Legal Tech</title>
<link href="https://fonts.googleapis.com/css2?family=Open+Sans:wght@400;600;700&display=swap" rel="stylesheet">
<style>
:root{
  --navy:#17365f;
  --ink:#333333;
  --muted:#8a8a8a;
  --line:#cfcfcf;
  --soft:#f5f5f5;
  --white:#ffffff;
  --footer:#464646;
  --footer-bar:#3f3f3f;
  --footer-text:#d6d6d6;
}
*{box-sizing:border-box;margin:0;padding:0}
html,body{width:1200px;height:2459px;overflow:hidden}
body{font-family:"Open Sans",Arial,sans-serif;color:var(--ink);background:var(--white);position:relative}
a{color:inherit;text-decoration:none}

/* header */
.site-header{position:absolute;top:0;left:0;width:1200px;height:108px;background:var(--white)}
.brand{position:absolute;left:131px;top:32px;display:flex;align-items:center;gap:12px;font-size:40px;font-weight:700;letter-spacing:3px;color:#3a3a3a;line-height:1}
.brand-mark{width:14px;height:14px;background:var(--navy)}
.main-nav{position:absolute;right:131px;top:46px;display:flex;gap:29px;font-size:11.5px;text-transform:uppercase;color:#555}
.main-nav .active{color:var(--navy);font-weight:600}

/* hero */
.hero{position:absolute;top:108px;left:0;width:1200px;height:505px;
  background:linear-gradient(180deg,#4f86c6 0%,#8bb4de 30%,#c9d8e8 55%,#e9eef4 75%,#f4f6f9 100%)}
.hero-arrow{position:absolute;top:239px;width:24px;height:29px;background:#2a2a2a;display:flex;align-items:center;justify-content:center}
.hero-arrow.prev{left:0}
.hero-arrow.next{right:0}

/* shared */
.section-title{font-size:24px;font-weight:700;color:var(--navy);text-transform:uppercase;text-align:center}
.btn-outline{display:inline-flex;align-items:center;justify-content:center;border:1px solid var(--line);background:var(--white);color:#555}

/* welcome */
.welcome{position:absolute;top:613px;left:0;width:1200px;height:331px;text-align:center}
.welcome .section-title{margin-top:76px}
.welcome p{width:938px;margin:16px auto 0;font-size:11.5px;line-height:20.5px;color:#555}
.welcome .btn-outline{margin-top:22px;width:88px;height:36px;font-size:11.5px}

/* services */
.services{position:absolute;top:944px;left:0;width:1200px;height:406px;background:var(--soft)}
.services .section-title{margin-top:76px}
.service-list{position:absolute;top:144px;left:131px;width:938px;display:flex;justify-content:space-between}
.service{width:214px;text-align:center}
.service-icon{height:44px;display:flex;align-items:flex-end;justify-content:center}
.service h3{margin-top:12px;font-size:20.5px;font-weight:600;color:var(--navy);text-transform:uppercase}
.service p{margin-top:4px;font-size:10.5px;line-height:16.5px;color:#666}
.service .btn-outline{margin-top:17px;width:82px;height:36px;font-size:9.5px;text-transform:uppercase;color:#888}

/* blog */
.blog{position:absolute;top:1350px;left:0;width:1200px;height:551px}
.blog-title{position:absolute;left:131px;top:80px;font-size:24px;font-weight:700;color:var(--navy);text-transform:uppercase}
.blog-controls{position:absolute;left:1015px;top:82px;display:flex;gap:7px}
.blog-controls span{width:23px;height:22px;border:1px solid #999;display:flex;align-items:center;justify-content:center}
.post{position:absolute;top:128px;width:298px}
.post-media{width:298px;height:181px;position:relative}
.post h4{margin-top:14px;font-size:15.5px;font-weight:400;line-height:22px;color:#333}
.post p{margin-top:8px;font-size:10.5px;line-height:17.5px;color:#8a8a8a;text-align:justify}
.post-meta{margin-top:14px;display:flex;gap:22px;font-size:10.5px;color:#777;align-items:center}
.post-meta span{display:flex;align-items:center;gap:5px}
.play{position:absolute;left:127px;top:68px;width:44px;height:44px;border-radius:50%;background:var(--white);display:flex;align-items:center;justify-content:center}

/* team */
.team{position:absolute;top:1901px;left:0;width:1200px;height:285px;background:var(--soft)}
.team .section-title{margin-top:63px}
.member{position:absolute;top:117px;display:flex;gap:11px}
.member-photo{width:97px;height:96px;flex:none}
.member h3{font-size:16px;font-weight:600;text-transform:uppercase;color:#333;margin-top:0}
.member .role{font-size:11px;color:#333;margin-top:4px}
.member p{margin-top:10px;font-size:10.5px;line-height:17px;color:#8a8a8a}
.member p a{color:#333;font-weight:600;margin-left:4px}

/* footer */
.site-footer{position:absolute;top:2186px;left:0;width:1200px;height:210px;background:var(--footer);color:var(--footer-text)}
.footer-heading{position:absolute;top:42px;font-size:15.5px;color:var(--white);font-weight:400}
.contact-list{position:absolute;left:133px;top:76px;list-style:none;font-size:10.5px;line-height:15px}
.contact-list li{display:flex;gap:12px;margin-bottom:8px}
.contact-list svg{flex:none;margin-top:2px}
.footer-map{position:absolute;left:333px;top:76px;width:185px;height:100px;background:linear-gradient(135deg,#e4e4e4,#cfcfcf)}
.link-col{position:absolute;top:76px;list-style:none;font-size:10.5px;line-height:22.5px}
.link-col li::before{content:"•";margin-right:6px;color:#aaa}
.social{position:absolute;left:974px;top:74px;display:grid;grid-template-columns:24px 24px;gap:9px 8px}
.social span{width:24px;height:24px;border-radius:50%}
.footer-bar{position:absolute;top:2396px;left:0;width:1200px;height:63px;background:var(--footer-bar);border-top:1px solid #555;color:#cfcfcf;font-size:10.5px;display:flex;align-items:center;justify-content:center}
</style>
</head>
<body>

<header class="site-header">
  <a class="brand" href="#"><span class="brand-mark"></span>KOVA</a>
  <nav class="main-nav">
    <a class="active" href="#">Home</a>
    <a href="#">Services</a>
    <a href="#">Team</a>
    <a href="#">Careers</a>
    <a href="#">Blog</a>
    <a href="#">Contact us</a>
  </nav>
</header>

<section class="hero" role="img" aria-label="Snow-covered mountain range under a blue sky with clouds">
  <span class="hero-arrow prev"><svg width="10" height="16" viewBox="0 0 10 16"><path d="M8 1 2 8l6 7" fill="none" stroke="#fff" stroke-width="1.5"/></svg></span>
  <span class="hero-arrow next"><svg width="10" height="16" viewBox="0 0 10 16"><path d="M2 1l6 7-6 7" fill="none" stroke="#fff" stroke-width="1.5"/></svg></span>
</section>

<section class="welcome">
  <h2 class="section-title">Welcome to KOVA</h2>
  <p>Donec facilisis volutpat lorem, at euismod velit dignissim ac. Class aptent taciti sociosqu ad litora torquent per conubia nostra, per inceptos himenaeos. Nulla consequat ipsum id mi placerat viverra. Sed tempor ex id dui sagittis, at luctus tortor finibus. Vestibulum ante ipsum primis in faucibus orci luctus et ultrices posuere cubilia Curae; Duis varius condimentum tellus, a faucibus lorem vestibulum eu. Duis sit amet tellus nisl. Maecenas nec metus sodales ante sollicitudin auctor in quis velit. Maecenas libero nisi, dignissim eget nibh a, mollis eleifend tellus. Fusce maximus porttitor libero vitae viverra.</p>
  <a class="btn-outline" href="#">Read more</a>
</section>

<section class="services">
  <h2 class="section-title">Our Services</h2>
  <div class="service-list">
    <div class="service">
      <div class="service-icon"><svg width="44" height="40" viewBox="0 0 44 40" fill="#17365f"><circle cx="22" cy="9" r="7"/><circle cx="9" cy="14" r="5"/><circle cx="35" cy="14" r="5"/><path d="M11 40V27a11 11 0 0 1 22 0v13z"/><path d="M0 34v-7a8 8 0 0 1 12-7 14 14 0 0 0-3 8v6z"/><path d="M44 34v-7a8 8 0 0 0-12-7 14 14 0 0 1 3 8v6z"/></svg></div>
      <h3>Family Law</h3>
      <p>Duis varius ate condimentum tellus, faucibus lorem vestibulum eu. Duis sit amet tellus nisl. Maecenas nec metus sodales.</p>
      <a class="btn-outline" href="#">Read more</a>
    </div>
    <div class="service">
      <div class="service-icon"><svg width="46" height="38" viewBox="0 0 46 38" fill="#17365f"><path d="M16 3h14v5h-3V6h-8v2h-3z"/><rect x="0" y="9" width="46" height="29" rx="4"/><rect x="0" y="20" width="46" height="2" fill="#f5f5f5"/><rect x="20" y="18" width="6" height="6" rx="1"/></svg></div>
      <h3>Business Law</h3>
      <p>Duis varius ate condimentum tellus, faucibus lorem vestibulum eu. Duis sit amet tellus nisl. Maecenas nec metus sodales.</p>
      <a class="btn-outline" href="#">Read more</a>
    </div>
    <div class="service">
      <div class="service-icon"><svg width="50" height="38" viewBox="0 0 50 38" fill="#17365f"><path d="M10 4q1-4 5-4h20q4 0 5 4l4 12h2q4 0 4 4v10H0V20q0-4 4-4h2z"/><path d="M13 6h24l3 10H10z" fill="#f5f5f5"/><rect x="4" y="28" width="10" height="10" rx="2"/><rect x="36" y="28" width="10" height="10" rx="2"/><circle cx="9" cy="23" r="3" fill="#f5f5f5"/><circle cx="41" cy="23" r="3" fill="#f5f5f5"/></svg></div>
      <h3>Vehicle Law</h3>
      <p>Duis varius ate condimentum tellus, faucibus lorem vestibulum eu. Duis sit amet tellus nisl. Maecenas nec metus sodales.</p>
      <a class="btn-outline" href="#">Read more</a>
    </div>
    <div class="service">
      <div class="service-icon"><svg width="52" height="36" viewBox="0 0 52 36"><rect x="1.5" y="1.5" width="49" height="33" fill="none" stroke="#17365f" stroke-width="3"/><rect x="6" y="6" width="40" height="24" fill="#17365f"/><circle cx="26" cy="18" r="9" fill="#f5f5f5"/><path d="M24 13h3v10h2v2h-6v-2h2v-7h-1z" fill="#17365f"/></svg></div>
      <h3>Debt Law</h3>
      <p>Duis varius ate condimentum tellus, faucibus lorem vestibulum eu. Duis sit amet tellus nisl. Maecenas nec metus sodales.</p>
      <a class="btn-outline" href="#">Read more</a>
    </div>
  </div>
</section>

<section class="blog">
  <h2 class="blog-title">Blog</h2>
  <div class="blog-controls">
    <span><svg width="6" height="10" viewBox="0 0 6 10"><path d="M5 1 1 5l4 4" fill="none" stroke="#555"/></svg></span>
    <span><svg width="6" height="10" viewBox="0 0 6 10"><path d="M1 1l4 4-4 4" fill="none" stroke="#555"/></svg></span>
  </div>

  <article class="post" style="left:131px">
    <div class="post-media" role="img" aria-label="Columned courthouse facade under a cloudy sky" style="background:linear-gradient(180deg,#6f86a8 0%,#9aa5b4 40%,#6b6d72 100%)"></div>
    <h4>Donec scelerisque felis at ante rhoncus, non mattis nulla facilisis</h4>
    <p>Integer gravida risus risus, in imperdiet leo convallis sed. Aenean lobortis neque, vitae faucibus lorem. Nulla dignissim tempus nisi, sed lobortis velit faucibus at. Fusce vel rutrum erat. Vivamus blandit interdum egestas.</p>
    <div class="post-meta">
      <span><svg width="10" height="9" viewBox="0 0 10 9"><path d="M5 9 1 5a2.4 2.4 0 0 1 4-3 2.4 2.4 0 0 1 4 3z" fill="#666"/></svg>(28)</span>
      <span><svg width="10" height="10" viewBox="0 0 10 10"><path d="M0 4h2v6H0zM3 4l2-4q2 0 1.5 3H10l-1 7H3z" fill="#666"/></svg>(21)</span>
      <span><svg width="10" height="10" viewBox="0 0 10 10"><rect x=".5" y="1.5" width="9" height="8" fill="none" stroke="#666"/><path d="M0 1h10v2H0z" fill="#666"/></svg>8 Feb, 2017</span>
    </div>
  </article>

  <article class="post" style="left:452px">
    <div class="post-media" role="img" aria-label="Hands stamping a document beside a scales of justice statue" style="background:linear-gradient(135deg,#3a3d44 0%,#cfcfd2 45%,#f2f2f2 70%,#8d7a5e 100%)"></div>
    <h4>Donec scelerisque felis at ante rhoncus, non mattis nulla facilisis</h4>
    <p>Aenean lobortis neque, vitae faucibus lorem. Nulla dignissim tempus nisi, sed lobortis velit faucibus at. Fusce vel rutrum erat. Vivamus blandit interdum egestas.</p>
    <div class="post-meta">
      <span><svg width="10" height="9" viewBox="0 0 10 9"><path d="M5 9 1 5a2.4 2.4 0 0 1 4-3 2.4 2.4 0 0 1 4 3z" fill="#666"/></svg>(28)</span>
      <span><svg width="10" height="10" viewBox="0 0 10 10"><path d="M0 4h2v6H0zM3 4l2-4q2 0 1.5 3H10l-1 7H3z" fill="#666"/></svg>(21)</span>
      <span><svg width="10" height="10" viewBox="0 0 10 10"><rect x=".5" y="1.5" width="9" height="8" fill="none" stroke="#666"/><path d="M0 1h10v2H0z" fill="#666"/></svg>8 Feb, 2017</span>
    </div>
  </article>

  <article class="post" style="left:770px">
    <div class="post-media" role="img" aria-label="Old town riverside with a cathedral at dusk" style="background:linear-gradient(180deg,#4a5a78 0%,#8a6a5a 45%,#5a4a3e 70%,#3a4656 100%)">
      <span class="play"><svg width="16" height="18" viewBox="0 0 16 18"><path d="M2 1l13 8-13 8z" fill="#222"/></svg></span>
    </div>
    <h4>Donec scelerisque felis at ante rhoncus, non mattis nulla facilisis</h4>
    <p>Aenean lobortis neque, vitae faucibus lorem. Nulla dignissim tempus nisi, sed lobortis velit faucibus at. Fusce vel rutrum erat. Vivamus blandit interdum egestas.</p>
    <div class="post-meta">
      <span><svg width="10" height="9" viewBox="0 0 10 9"><path d="M5 9 1 5a2.4 2.4 0 0 1 4-3 2.4 2.4 0 0 1 4 3z" fill="#666"/></svg>(28)</span>
      <span><svg width="10" height="10" viewBox="0 0 10 10"><path d="M0 4h2v6H0zM3 4l2-4q2 0 1.5 3H10l-1 7H3z" fill="#666"/></svg>(21)</span>
      <span><svg width="10" height="10" viewBox="0 0 10 10"><rect x=".5" y="1.5" width="9" height="8" fill="none" stroke="#666"/><path d="M0 1h10v2H0z" fill="#666"/></svg>8 Feb, 2017</span>
    </div>
  </article>
</section>

<section class="team">
  <h2 class="section-title">Our Team</h2>
  <div class="member" style="left:131px;width:460px">
    <div class="member-photo" role="img" aria-label="Portrait photo of a team member" style="background:linear-gradient(180deg,#d9d9d9,#8c8c8c)"></div>
    <div>
      <h3>Marc Keller</h3>
      <div class="role">Duis sed congue nibh</div>
      <p>Aenean lobortis neque, vitae faucibus lorem. Nulla dignissim tempus nisi, sed lobortis velit faucibus at. Fusce vel rutrum erat. Vivamus blandit interdum egestas.<a href="#">More</a></p>
    </div>
  </div>
  <div class="member" style="left:628px;width:441px">
    <div class="member-photo" role="img" aria-label="Portrait photo of a team member" style="background:linear-gradient(180deg,#e4ddd4,#b39a7e)"></div>
    <div>
      <h3>Lena</h3>
      <div class="role">Duis sed congue nibh</div>
      <p>Aenean lobortis neque, vitae faucibus lorem. Nulla dignissim tempus nisi, sed lobortis velit faucibus at. Fusce vel rutrum erat. Vivamus blandit interdum egestas.<a href="#">More</a></p>
    </div>
  </div>
</section>

<footer class="site-footer">
  <h4 class="footer-heading" style="left:133px">Contact info</h4>
  <ul class="contact-list">
    <li><svg width="8" height="11" viewBox="0 0 8 11"><path d="M4 11 .6 5.5A4 4 0 1 1 7.4 5.5z" fill="#ccc"/><circle cx="4" cy="4" r="1.4" fill="#464646"/></svg><span>24 Building name, Street name<br>City - Zipcode</span></li>
    <li><svg width="8" height="11" viewBox="0 0 8 11"><rect x=".5" y=".5" width="7" height="10" rx="1" fill="none" stroke="#ccc"/></svg><span>564 310 2291</span></li>
    <li><svg width="10" height="9" viewBox="0 0 10 9"><rect x="0" y="3" width="10" height="6" fill="#ccc"/><rect x="2" y="0" width="6" height="3" fill="#ccc"/></svg><span>324 650 7734</span></li>
    <li><svg width="10" height="8" viewBox="0 0 10 8"><rect width="10" height="8" fill="#ccc"/><path d="M0 0l5 4 5-4" fill="none" stroke="#464646"/></svg><span>info@kova.ch</span></li>
  </ul>
  <div class="footer-map" role="img" aria-label="Street map of the office location"></div>

  <h4 class="footer-heading" style="left:644px">Links</h4>
  <ul class="link-col" style="left:644px">
    <li>Home</li><li>Services</li><li>Team</li><li>Careers</li><li>Blog</li>
  </ul>
  <ul class="link-col" style="left:741px">
    <li>Contact us</li><li>Terms and conditions</li><li>Privacy Policy</li><li>Sitemap</li>
  </ul>

  <h4 class="footer-heading" style="left:974px">Social Media</h4>
  <div class="social">
    <span style="background:#4a63a3"></span>
    <span style="background:#3aa6e8"></span>
    <span style="background:#1b79b3"></span>
    <span style="background:#d9473a"></span>
  </div>
</footer>
<div class="footer-bar">Copyright © 2017 Company name. All rights reserved.</div>

</body>
</html>
```